Simple and clean

We need a business card design for a new company called Dwelling Hawk. It is a search engine to find current properties for sale or rent in New Zealand market.
We have already a colour scheme that we would like people to use.
Light brown: #D4CCB0
Light green: #D6E4D4
Green: #669966
Black/White
It is OK to divert from this colour scheme slightly as long as there is a green component to the business card.
Final design should be clean, simple and should communicate the nature of the business.
Target Market(s)
- First home buyers
- Real estate agents
- People seeking rentals
Industry/Entity Type
Business
Requirements
Must have
- Use those or similar colours.
Light brown: #D4CCB0
Light green: #D6E4D4
Green: #669966
Black/White

```html
<!DOCTYPE html>
<html lang="en">
<head>
<meta charset="utf-8">
<title>Dwelling Hawk – Business Card</title>
<link rel="stylesheet" href="https://fonts.googleapis.com/css2?family=Arimo:wght@700&display=swap">
<style>
  :root {
    --page-bg: #ffffff;
    --card-light: #c8e8c0;
    --card-mid: #b4dcac;
    --panel-light: #b6dfae;
    --panel-dark: #98cc8f;
    --ink-green: #3f7d3f;
    --ink-deep: #245a2a;
    --emboss-light: rgba(255, 255, 255, 0.55);
    --shadow: rgba(20, 50, 20, 0.35);
  }
  * { box-sizing: border-box; margin: 0; padding: 0; }
  html, body {
    width: 1200px;
    height: 899px;
    overflow: hidden;
    background: var(--page-bg);
    font-family: "Arimo", Arial, sans-serif;
    font-weight: 700;
  }
  .business-card {
    position: absolute;
    left: 150px;
    top: 192px;
    width: 900px;
    height: 514px;
    background: linear-gradient(160deg, var(--card-light) 0%, var(--card-mid) 100%);
    box-shadow: 0 18px 40px var(--shadow);
    overflow: hidden;
  }
  .brand {
    position: absolute;
    left: 0;
    top: 0;
    width: 120px;
    height: 514px;
  }
  .brand-name {
    position: absolute;
    left: 60px;
    top: 220px;
    transform: translate(-50%, -50%) rotate(-90deg);
    white-space: nowrap;
    font-size: 46px;
    color: var(--ink-deep);
  }
  .brand-dot {
    position: absolute;
    left: 30px;
    top: 420px;
    width: 60px;
    height: 60px;
    border-radius: 50%;
    background: var(--ink-deep);
  }
  .holder {
    position: absolute;
    left: 190px;
    top: 92px;
    width: 490px;
    text-align: center;
    color: var(--ink-green);
    text-shadow: 1px 1px 0 var(--emboss-light), -1px -1px 1px rgba(0,0,0,0.25);
  }
  .holder-name { font-size: 56px; line-height: 1.05; }
  .holder-role { font-size: 30px; line-height: 1.1; }
  .contact-panel {
    position: absolute;
    left: 165px;
    top: 245px;
    width: 735px;
    height: 245px;
    background: linear-gradient(180deg, var(--panel-light) 0%, var(--panel-dark) 100%);
    box-shadow: -4px 12px 22px var(--shadow);
    color: var(--ink-green);
    text-shadow: 1px 1px 0 var(--emboss-light), -1px -1px 1px rgba(0,0,0,0.25);
  }
  .contact-phone {
    position: absolute;
    left: 150px;
    top: 22px;
    font-size: 34px;
  }
  .contact-email {
    position: absolute;
    left: 18px;
    top: 70px;
    font-size: 33px;
    letter-spacing: -0.5px;
  }
  .contact-web {
    position: absolute;
    left: 80px;
    top: 168px;
    font-size: 36px;
    letter-spacing: -0.5px;
    color: var(--ink-deep);
  }
</style>
</head>
<body>
  <main class="business-card">
    <div class="brand">
      <span class="brand-dot"></span>
      <span class="brand-name">Dwelling Hawk</span>
    </div>
    <div class="holder">
      <p class="holder-name">Sam Carter</p>
      <p class="holder-role">Director</p>
    </div>
    <section class="contact-panel">
      <p class="contact-phone">000 000 000</p>
      <p class="contact-email">samcarter@hawkmail.co.nz</p>
      <p class="contact-web">www.dwellinghawk.co.nz</p>
    </section>
  </main>
</body>
</html>
```